Tavenhurst Falcons FC Website

We are looking to develop a new website for Tavenhurst FC. Tavenhurst FC has now joined with Tavenhurst Falcons FC and we are looking at a website that can work for both clubs. Tavenhurst FC play in a local park football competition while tavenhurst Falcons are a Semi Professional team that plays in the Ostral Premier Series Competition. What we are after is two separate website off the one platform. I have attached both team logos for you to visualise. Also you can look at the existing tavenhurst website www.tavenhurstfc.net.au. We are looking for a huge improvement in the website and it will be imperative we have links to sponsors and the sponsors can get regular visuals. Weare looking to move this club forward and have a very professional website that can communicate clearly with the community.

Hi All,

Please remember that the website is to represent two clubs;
1. Tavenhurst Falcons FC (Competes in Semi Professional League)
2. Tavenhurst FC (Compete in KPWLT League which is a lower level)

Further to this the Tavenhurst Falcons FC page will require a player profile page which will show photos of each player and a little bio on each.

Thanks

Reason: Would like to spend more time review existing and new designs

```html
<!DOCTYPE html>
<html lang="en">
<head>
<meta charset="utf-8">
<title>Tavenhurst Falcons FC</title>
<link href="https://fonts.googleapis.com/css2?family=Arimo:wght@400;700&family=Roboto+Condensed:wght@400;700&display=swap" rel="stylesheet">
<style>
:root{
  --pitch:#3f9a2b;
  --pitch-light:#46a430;
  --band:rgba(30,90,20,.55);
  --footer:#2f7d21;
  --red:#d5161c;
  --red-dark:#a80f14;
  --white:#ffffff;
  --line:rgba(255,255,255,.45);
  --ink:#333333;
}
*{margin:0;padding:0;box-sizing:border-box}
html,body{width:910px;height:1200px;overflow:hidden}
body{
  position:relative;
  font-family:"Arimo",Arial,sans-serif;
  color:var(--white);
  background:repeating-linear-gradient(90deg,var(--pitch) 0 46px,var(--pitch-light) 46px 92px);
}
a{color:inherit}
.abs{position:absolute}

/* header */
.club-mark{left:126px;top:14px;width:82px;height:82px;border-radius:50%;background:var(--white);border:4px solid var(--red)}
.club-title{left:226px;top:35px;font-size:21px;font-weight:700}
.club-sub{left:226px;top:58px;font-size:12.5px}
.register{left:595px;top:36px;width:107px;height:23px;background:var(--red);border:2px solid #ff3a3a;outline:1px solid var(--red-dark);font-size:9.5px;display:flex;align-items:center;justify-content:center;letter-spacing:.2px}
.social{display:flex;gap:6px;align-items:center;font-size:8.5px}
.social span{display:flex;align-items:center;gap:3px}
.social i{width:9px;height:9px;border-radius:50%;background:var(--red);border:1.5px solid var(--white);display:inline-block}
.header-social{left:712px;top:42px}
.top-links{left:612px;top:88px;display:flex;align-items:center;gap:19px;font-size:9px}
.main-nav{left:122px;top:114px;width:667px;height:31px;background:var(--white);padding:3px;display:flex}
.main-nav a{display:flex;align-items:center;padding:0 8px;font-size:9.2px;color:#555;text-decoration:none;border-right:1px solid #ddd;text-transform:uppercase}
.main-nav a.active{background:var(--red);color:var(--white);padding:0 10px}
.main-nav a:last-child{border-right:0}

/* hero */
.hero{left:0;top:146px;width:910px;height:332px;background:linear-gradient(180deg,#bdbfa9 0%,#a3a583 45%,#6f7a3c 75%,#4d5b22 100%)}
.hero-arrow{top:295px;width:34px;height:34px;background:rgba(40,40,40,.7);border:1px solid #ddd;display:flex;align-items:center;justify-content:center}
.hero-caption{left:367px;top:295px;width:175px;height:33px;background:rgba(20,20,20,.8);border:1px solid #aaa;font-family:"Roboto Condensed",sans-serif;font-size:15.5px;display:flex;align-items:center;justify-content:center}

/* section headings */
.section-head{height:32px;background:var(--band);display:flex;align-items:center;padding-left:14px;font-size:17px}
.section-head b{margin-left:5px}
.btn-light{background:var(--white);color:var(--red);font-size:8.5px;display:flex;align-items:center;justify-content:center;height:16px;text-decoration:none}

/* welcome */
.welcome{left:122px;top:506px;width:401px}
.welcome ul{list-style:none;margin-top:12px;font-size:8.3px;line-height:10.5px}
.welcome li{position:relative;padding-left:10px;margin-bottom:8px}
.welcome li:before{content:"";position:absolute;left:1px;top:4px;width:3px;height:3px;border-radius:50%;background:var(--white)}

/* member promo */
.member{left:559px;top:506px;width:230px;height:180px;background:linear-gradient(135deg,#b3121a,#d8202a 55%,#e6303a)}
.member-text{right:18px;top:32px;text-align:right;font-size:17px;line-height:19px}
.member-text .year{font-size:25px;font-weight:700;line-height:32px}
.join{left:704px;top:628px;width:68px;height:20px;font-size:9px;font-weight:700}

/* top news */
.top-news{left:122px;top:714px;width:401px}
.pager{margin-left:auto;margin-right:12px;display:flex;gap:6px}
.news-item{left:122px;width:401px;display:flex;gap:14px}
.news-thumb{width:73px;height:74px;border:2px solid var(--white);flex:none}
.news-body{font-size:8.3px;line-height:10.5px}
.news-body h3{font-size:8.5px;font-weight:700;line-height:10.5px;margin-bottom:8px}
.read-more{display:flex;align-items:center;gap:6px;margin-top:10px;font-size:9px}
.read-more i{width:13px;height:13px;border-radius:50%;background:var(--white);display:flex;align-items:center;justify-content:center}

/* fixtures */
.fixtures{left:559px;top:711px;width:230px}
.fx-table{left:559px;top:757px;width:230px;border:1px solid var(--line);font-size:9px}
.fx-tabs{display:flex;font-weight:700}
.fx-tabs span{padding:0 7px;height:22px;display:flex;align-items:center;border-right:1px solid var(--line);border-bottom:1px solid var(--line)}
.fx-tabs .on{background:var(--red)}
.fx-tabs2{height:23px;display:flex;align-items:center;padding-left:7px;font-weight:700;width:86px;border-right:1px solid var(--line)}
.fx-cols{display:flex;background:rgba(30,90,20,.25);border-top:1px solid var(--line)}
.fx-col{flex:1;border-right:1px dashed var(--line)}
.fx-col:last-child{border-right:0}
.fx-col h4{font-weight:400;font-size:9.5px;height:23px;display:flex;align-items:center;padding-left:13px;background:var(--band);border-bottom:1px solid var(--line)}
.fx-col ul{list-style:none;padding:12px 0 26px 13px;line-height:14.5px;font-size:8.5px}
.fx-col li:before{content:"» ";font-size:10px}

/* footer */
.footer{left:0;top:1002px;width:910px;height:114px;background:var(--footer)}
.foot-col{top:1022px;font-size:8.5px;line-height:10.5px}
.foot-col h5{font-size:9px;font-weight:700;margin-bottom:10px;letter-spacing:.3px}
.foot-col ul{list-style:none}
.foot-col li:before{content:"• "}
.divider{top:1022px;width:1px;height:56px;border-left:1px dashed var(--line)}
.sponsor{top:1044px;width:82px;height:38px;background:var(--white);color:#7a1a1a;font-size:8px;font-weight:700;display:flex;align-items:center;justify-content:center;text-align:center;line-height:10px}
.view-all{left:740px;top:1019px;display:flex;align-items:center;gap:5px;font-size:8.5px}
.view-all i{width:13px;height:13px;border-radius:50%;background:var(--white);display:flex;align-items:center;justify-content:center}

.copyright{left:0;top:1133px;width:910px;text-align:center;font-size:8.6px;line-height:11px}
.copyright a{color:#f2d37a}
.footer-social{left:0;top:1171px;width:910px;justify-content:center}
</style>
</head>
<body>

<header>
  <div class="abs club-mark" role="img" aria-label="Club crest"></div>
  <h1 class="abs club-title">Tavenhurst Falcons FC</h1>
  <p class="abs club-sub">The Official Website of Tavenhurst Falcons FC</p>
  <a class="abs register">REGISTER ONLINE</a>
  <div class="abs social header-social"><span><i></i>Fanpage</span><span><i></i>Chirp</span><span><i></i>Proflink</span></div>
  <nav class="abs top-links">
    <svg width="18" height="16" viewBox="0 0 18 16" aria-label="Home"><path d="M9 1 L17 8 H14 V15 H10.5 V10.5 H7.5 V15 H4 V8 H1 Z" fill="#fff"/></svg>
    <a>About Us</a><a>Media</a><a>Contact Us</a>
  </nav>
  <nav class="abs main-nav">
    <a class="active">Latest News</a><a>Fixture &amp; Results</a><a>History</a><a>Profile</a><a>Management</a><a>Squad</a><a>Membership</a><a>Gallery</a><a>Video</a><a>Sponsors</a>
  </nav>
</header>

<section>
  <div class="abs hero" role="img" aria-label="Action photo of a striker and a diving goalkeeper reaching for the ball on a muddy pitch"></div>
  <div class="abs hero-arrow" style="left:36px"><svg width="12" height="18"><path d="M10 1 L2 9 L10 17" stroke="#fff" stroke-width="2" fill="none"/></svg></div>
  <div class="abs hero-arrow" style="left:834px"><svg width="12" height="18"><path d="M2 1 L10 9 L2 17" stroke="#fff" stroke-width="2" fill="none"/></svg></div>
  <div class="abs hero-caption">The&nbsp;<b>Game</b>&nbsp;Is About&nbsp;<b>Glory</b></div>
</section>

<section class="abs welcome">
  <h2 class="section-head" style="font-weight:400">Welcome to<b>Tavenhurst Falcons FC</b></h2>
  <ul>
    <li>Lorem ipsum dolor sit amet, consectetur adipisicing elit, sed do eiusmod tempor incididunt ut labore et dolore magna aliqua.</li>
    <li>Lorem ipsum dolor sit amet, consectetur adipisicing elit.</li>
    <li>Lorem ipsum dolor sit amet, consectetur adipisicing elit, sed do eiusmod tempor incididunt ut labore et dolore magna aliqua.</li>
    <li>Lorem ipsum dolor sit amet, consectetur adipisicing elit, sed do eiusmod tempor incididunt ut labore et dolore magna aliqua. Ut enim ad minim veniam, quis nostrud exercitation ullamco laboris nisi ut aliquip ex ea commodo consequat.</li>
  </ul>
  <a class="btn-light" style="width:54px;margin-top:10px">Read More</a>
</section>

<aside>
  <div class="abs member" role="img" aria-label="Red promotional photo of a club medal and kit"></div>
  <div class="abs member-text" style="right:121px;top:532px">BECOME<br>A MEMBER<div class="year">2014</div></div>
  <a class="abs btn-light join">JOIN NOW</a>
</aside>

<section>
  <h2 class="abs section-head top-news" style="font-weight:400">Top<b>News</b>
    <span class="pager"><svg width="8" height="12"><path d="M7 1 L2 6 L7 11" stroke="#ddd" stroke-width="2" fill="none"/></svg><svg width="8" height="12"><path d="M1 1 L6 6 L1 11" stroke="#fff" stroke-width="2" fill="none"/></svg></span>
  </h2>
  <article class="abs news-item" style="top:758px">
    <div class="news-thumb" role="img" aria-label="Coach in an orange bib on the training field" style="background:linear-gradient(160deg,#9fb7d8,#e07a3a 55%,#5b8a3a)"></div>
    <div class="news-body">
      <h3>Lorem ipsum dolor sit amet, consectetur adipisicing elit, sed do eiusmod tempor incididunt ut labore et dolore magna aliqua.</h3>
      <p>Lorem Ipsum is simply dummy text of the printing and typesetting industry. Lorem Ipsum has been the industry's standard dummy text ever since the 1500s....</p>
      <a class="read-more"><i><svg width="6" height="8"><path d="M1 1 L5 4 L1 7" stroke="#d5161c" stroke-width="1.6" fill="none"/></svg></i><u>Read More</u></a>
    </div>
  </article>
  <article class="abs news-item" style="top:861px">
    <div class="news-thumb" role="img" aria-label="Junior players in red kits during a match" style="background:linear-gradient(160deg,#cfd8c4,#c9453a 50%,#6a9a44)"></div>
    <div class="news-body">
      <h3>Lorem ipsum dolor sit amet, consectetur adipisicing elit, sed do eiusmod tempor incididunt ut labore et dolore magna aliqua.</h3>
      <p>Lorem Ipsum is simply dummy text of the printing and typesetting industry. Lorem Ipsum has been the industry's standard dummy text ever since the 1500s....</p>
      <a class="read-more"><i><svg width="6" height="8"><path d="M1 1 L5 4 L1 7" stroke="#d5161c" stroke-width="1.6" fill="none"/></svg></i><u>Read More</u></a>
    </div>
  </article>
  <a class="abs btn-light" style="left:122px;top:958px;width:54px">View All</a>
</section>

<section>
  <h2 class="abs section-head fixtures" style="font-weight:400">Fixtures &amp;<b>Results</b></h2>
  <div class="abs fx-table">
    <div class="fx-tabs"><span class="on">Premier League</span><span>Super League</span><span style="border-right:0;flex:1">Under 16 / 2</span></div>
    <div class="fx-tabs2">Under 17 / 1</div>
    <div class="fx-cols">
      <div class="fx-col"><h4>FIXTURES</h4><ul><li>Under 10 / 2</li><li>AA Men / 5</li><li>07 ECL / Red</li><li>06 / A Green</li></ul></div>
      <div class="fx-col"><h4>RESULTS</h4><ul><li>Under 10 / 3</li><li>AA Men / 6</li><li>07 ECL / Green</li><li>06 / B Blue</li></ul></div>
    </div>
  </div>
  <a class="abs btn-light" style="left:559px;top:944px;width:54px">View All</a>
</section>

<footer>
  <div class="abs footer"></div>
  <div class="abs foot-col" style="left:122px"><h5>HOME</h5><ul><li><u>News</u></li><li>Gallery</li><li>Sponsor</li><li>Contact Us</li></ul></div>
  <div class="abs divider" style="left:198px"></div>
  <div class="abs foot-col" style="left:225px"><h5>PROFILE</h5><ul><li>Management</li><li>History</li><li>Coach History</li><li>Awards</li></ul></div>
  <div class="abs divider" style="left:310px"></div>
  <div class="abs foot-col" style="left:342px"><h5>SPONSOR'S</h5></div>
  <a class="abs view-all"><i><svg width="6" height="8"><path d="M1 1 L5 4 L1 7" stroke="#d5161c" stroke-width="1.6" fill="none"/></svg></i><u>View All</u></a>
  <div class="abs sponsor" style="left:342px">Brightfield Media</div>
  <div class="abs sponsor" style="left:433px">Harlow Venn &amp; Co</div>
  <div class="abs sponsor" style="left:524px">Ashcombe Group</div>
  <div class="abs sponsor" style="left:615px">Northgate Trophies</div>
  <div class="abs sponsor" style="left:706px">Kestrel Safety</div>

  <div class="abs copyright">Copyright © 2014. All Rights Reserved.<br><a><u>Privacy Policy</u></a></div>
  <div class="abs social footer-social" style="display:flex"><span><i></i>Fanpage</span><span><i></i>Chirp</span><span><i></i>Proflink</span></div>
</footer>

</body>
</html>
```